Cover page and letterhead for athlete development program

We require an exciting and dynamic cover page with a second page letterhead in a word doc format for us to use as professional stationery for letter merges and portfolio documents. We are an athlete preparation company that specialises in training up and coming sports representatives in the fitness and sports science industry. We work with athletes from ages 13 - 24 mainly. If we could have images on the cover page from the sports of:
Rugby League
Rugby Union
Hockey
Cricket
AFL
Soccer
Track and Field
Netball
Basketball
Golf
Weight training

This would be a great start. Thank you

```html
<!DOCTYPE html>
<html lang="en">
<head>
<meta charset="utf-8">
<title>Rising Sprint Letterhead</title>
<link rel="stylesheet" href="https://fonts.googleapis.com/css2?family=Arimo:wght@400;700&display=swap">
<style>
:root{
  --backdrop:#dde0e2;
  --paper:#ffffff;
  --ink:#8a8a8a;
  --dark:#1f1f1f;
  --gold:#c98a1c;
  --gold-light:#e9b35a;
}
*{margin:0;padding:0;box-sizing:border-box}
html,body{width:1200px;height:784px;overflow:hidden;background:var(--backdrop)}
body{display:flex;align-items:center;justify-content:center;font-family:"Arimo",Arial,sans-serif}
.letterhead{position:relative;width:556px;height:744px;background:var(--paper);box-shadow:0 4px 14px rgba(0,0,0,.18)}
.header-rule{position:absolute;top:30px;left:40px;width:150px;height:4px;background:linear-gradient(90deg,var(--gold),var(--gold-light),var(--gold))}
.brand{position:absolute;top:19px;left:208px;display:flex;align-items:center;gap:8px;white-space:nowrap}
.brand-mark{width:16px;height:16px;background:var(--gold)}
.brand-name{font-weight:700;font-size:18px;letter-spacing:1px;color:var(--dark);text-transform:uppercase}
.header-bar{position:absolute;top:26px;left:418px;right:0;height:12px;background:linear-gradient(180deg,#555,var(--dark) 60%,#888)}
.letter-body{position:absolute;top:92px;left:78px;width:404px;font-size:10.6px;line-height:1.42;color:var(--ink)}
.letter-body p{margin-bottom:14px}
.footer{position:absolute;left:0;right:0;bottom:0;height:74px}
.footer-band{position:absolute;left:0;right:0;bottom:22px;height:6px;background:linear-gradient(90deg,var(--dark),#666,var(--dark))}
.footer-rule{position:absolute;left:0;width:70%;bottom:30px;height:3px;background:var(--gold)}
.contact{position:absolute;left:26px;bottom:38px;display:flex;gap:18px;font-size:8px;color:#555;white-space:nowrap}
.contact span{display:flex;align-items:center;gap:4px}
.contact svg{width:9px;height:9px}
.web{position:absolute;right:0;bottom:0;width:166px;height:28px;background:var(--dark);color:#fff;font-size:11px;font-weight:700;display:flex;align-items:center;justify-content:center;clip-path:polygon(10% 0,100% 0,100% 100%,0 100%)}
</style>
</head>
<body>
<main class="letterhead">
  <div class="header-rule"></div>
  <div class="brand"><span class="brand-mark"></span><span class="brand-name">Rising Sprint</span></div>
  <div class="header-bar"></div>

  <section class="letter-body">
    <p>Lorem Ipsum is simply dummy text of the printing and typesetting industry. Lorem Ipsum has been the industry's standard dummy text ever since the 1500s, when an unknown printer took a galley of type and scrambled it to make a type specimen book. It has survived not only five centuries, but also the leap into electronic typesetting, remaining essentially unchanged. It was popularised in the 1960s with the release of Typeline sheets containing Lorem Ipsum passages, and more recently with desktop publishing software like PageFrame Studio including versions of Lorem Ipsum.</p>
    <p>It is a long established fact that a reader will be distracted by the readable content of a page when looking at its layout. The point of using Lorem Ipsum is that it has a more-or-less normal distribution of letters, as opposed to using 'Content here, content here', making it look like readable English. Many desktop publishing packages and web page editors now use Lorem Ipsum as their default model text, and a search for 'lorem ipsum' will uncover many web sites still in their infancy. Various versions have evolved over the years, sometimes by accident, sometimes on purpose (injected humour and the like).</p>
    <p>Contrary to popular belief, Lorem Ipsum is not simply random text. It has roots in a piece of classical Latin literature from 45 BC, making it over 2000 years old. Dana Whitlow, a Latin professor at Coastal Ridge College in Marlow, looked up one of the more obscure Latin words, consectetur, from a Lorem Ipsum passage, and going through the cites of the word in classical literature, discovered the undoubtable source. Lorem Ipsum comes from sections 1.10.32 and 1.10.33 of "de Finibus Bonorum et Malorum" structures, to generate Lorem Ipsum which looks reasonable. The generated Lorem Ipsum is therefore always free from repetition, injected humour, or non-characteristic words etc.</p>
  </section>

  <footer class="footer">
    <div class="contact">
      <span><svg viewBox="0 0 10 10"><circle cx="5" cy="5" r="5" fill="#333"/><circle cx="5" cy="4" r="1.6" fill="#fff"/></svg>12 Harbour Lane, Northfield, AU 0000</span>
      <span><svg viewBox="0 0 10 10"><circle cx="5" cy="5" r="5" fill="#333"/><rect x="3.5" y="2.5" width="3" height="5" rx=".6" fill="#fff"/></svg>002-555-0142</span>
      <span><svg viewBox="0 0 10 10"><circle cx="5" cy="5" r="5" fill="#333"/><rect x="2.5" y="3.5" width="5" height="3" fill="#fff"/></svg>002-555-0187</span>
      <span><svg viewBox="0 0 10 10"><circle cx="5" cy="5" r="5" fill="#333"/><path d="M2.5 3.5h5v3h-5z M2.5 3.5l2.5 2 2.5-2" fill="none" stroke="#fff" stroke-width=".8"/></svg>hello@risingsprint.com.au</span>
    </div>
    <div class="footer-rule"></div>
    <div class="footer-band"></div>
    <div class="web">www.risingsprint.com.au</div>
  </footer>
</main>
</body>
</html>
```